New Business Cards for Tormin Group

We need a new Business Card to compliment our new logo. We are a vibrant design, manufacture and install business providing recreation areas, public parks and Municipal spaces. We want business cards that are classy, modern and clean.

We have recently changed our logo, and are celebrating our 40th anniversary. We want business cards with a new modern design to reflect our status.

Target Market(s)

Customers

Contact Information for Business Card

We need all the details of our 3 offices as per the business card attached. Please disregard the old logo on the business card, the other three files show our new logo.

Requirements
Must have
• All info as per attached business card but with new logo.
Nice to have

```html
<!DOCTYPE html>
<html lang="en">
<head>
<meta charset="utf-8">
<title>Tormin Group – Business Card</title>
<link href="https://fonts.googleapis.com/css2?family=Roboto:wght@300;400;500&family=Roboto+Condensed:wght@400&display=swap" rel="stylesheet">
<style>
  :root {
    --bg: #e7e6e3;
    --paper: #fbfbfb;
    --paper-shade: #ececec;
    --slate: #46474b;
    --slate-dark: #3a3b3f;
    --red: #e8303f;
    --ink: #55565a;
    --ink-light: #8a8b8e;
    --white: #ffffff;
  }
  * { margin: 0; padding: 0; box-sizing: border-box; }
  html, body { width: 1200px; height: 1023px; overflow: hidden; background: var(--bg); }
  .canvas {
    width: 1200px; height: 1023px;
    display: flex; align-items: center; justify-content: center;
  }
  .card {
    position: relative;
    width: 1000px; height: 572px;
    border-radius: 26px;
    overflow: hidden;
    background: linear-gradient(180deg, var(--paper) 0%, var(--paper-shade) 100%);
    box-shadow: 0 12px 40px rgba(0,0,0,.18);
    font-family: "Roboto", Arial, sans-serif;
  }
  .card__top { position: absolute; inset: 0 0 auto 0; height: 300px; }
  .person { position: absolute; left: 62px; top: 78px; width: 440px; }
  .person__name {
    color: var(--red); font-weight: 400; font-size: 38px;
    letter-spacing: 1px; text-transform: uppercase; white-space: nowrap;
  }
  .person__role { color: var(--ink-light); font-size: 24px; font-weight: 300; margin: 4px 0 22px; }
  .contact { list-style: none; }
  .contact li {
    display: flex; align-items: center; gap: 14px;
    color: var(--ink); font-size: 23px; font-weight: 300; line-height: 38px;
  }
  .contact svg { width: 18px; height: 18px; flex: none; }
  .contact .accent { color: var(--red); }
  .brand {
    position: absolute; left: 540px; right: 50px; top: 80px;
    display: flex; align-items: center; justify-content: flex-end; gap: 18px;
  }
  .brand__dot { width: 90px; height: 90px; border-radius: 50%; background: var(--red); flex: none; }
  .brand__name {
    color: var(--slate); font-weight: 500; font-size: 42px; line-height: 1;
    text-transform: uppercase; letter-spacing: 1px; white-space: nowrap;
  }
  .rule { position: absolute; left: 0; right: 0; top: 300px; height: 5px; background: var(--red); }
  .card__offices {
    position: absolute; left: 0; right: 0; top: 305px; bottom: 0;
    background: linear-gradient(180deg, var(--slate) 0%, var(--slate-dark) 100%);
    display: grid; grid-template-columns: repeat(3, 1fr);
    padding: 36px 56px 0 62px; column-gap: 30px;
  }
  .office__title { color: var(--red); font-size: 26px; font-weight: 400; margin-bottom: 8px; }
  .office p {
    color: var(--white); font-family: "Roboto Condensed", Arial, sans-serif;
    font-size: 20px; line-height: 29px; white-space: nowrap;
  }
  .office .gap { margin-top: 20px; }
  .office b { color: var(--red); font-weight: 400; }
</style>
</head>
<body>
<main class="canvas">
  <article class="card">
    <section class="card__top">
      <div class="person">
        <h1 class="person__name">Marek Delhoven</h1>
        <p class="person__role">Managing Partner</p>
        <ul class="contact">
          <li>
            <svg viewBox="0 0 24 24"><path fill="#e8303f" d="M6.6 10.8a15 15 0 0 0 6.6 6.6l2.2-2.2a1 1 0 0 1 1-.25 11.4 11.4 0 0 0 3.6.57 1 1 0 0 1 1 1V20a1 1 0 0 1-1 1A17 17 0 0 1 3 4a1 1 0 0 1 1-1h3.5a1 1 0 0 1 1 1c0 1.250.2 2.450.57 3.570a1 1 0 0 1-.25 1z"/></svg>
            +971 (0)50 384 7126
          </li>
          <li>
            <svg viewBox="0 0 24 24"><rect x="2" y="5" width="20" height="14" rx="1.5" fill="none" stroke="#e8303f" stroke-width="2"/><path d="M3 6l9 7 9-7" fill="none" stroke="#e8303f" stroke-width="2"/></svg>
            marek@tormingroup.com
          </li>
          <li>
            <svg viewBox="0 0 24 24"><circle cx="12" cy="12" r="10" fill="#e8303f"/><path d="M2 12h20M12 2c3 3 3 17 0 20M12 2c-3 3-3 17 0 20" fill="none" stroke="#fff" stroke-width="1.4"/></svg>
            <span>www.<span class="accent">tormingroup</span>.com</span>
          </li>
        </ul>
      </div>
      <div class="brand">
        <span class="brand__dot"></span>
        <span class="brand__name">Tormin Group</span>
      </div>
    </section>
    <div class="rule"></div>
    <section class="card__offices">
      <div class="office">
        <h2 class="office__title">Head Office</h2>
        <p>P.O. Box:<br>41820 Abu Dhabi, U.A.E.</p>
        <p class="gap"><b>P</b> : +971 (0)2 5137702<br><b>F</b> : +971 (0)2 5137703<br><b>E</b> : sales@tormingroup.com</p>
      </div>
      <div class="office">
        <h2 class="office__title">Dubai Office</h2>
        <p>P.O. Box:<br>508214 Dubai, U.A.E.</p>
        <p class="gap"><b>P</b> : +971 (0)4 3826140<br><b>F</b> : +971 (0)4 3826141<br><b>E</b> : sales@tormingroup.com</p>
      </div>
      <div class="office">
        <h2 class="office__title">Qatar Office</h2>
        <p>P.O. Box:<br>27309 Doha, Qatar</p>
        <p class="gap"><b>P</b> : +974 44715830<br><b>F</b> : +974 44715831<br><b>E</b> : sales@tormingroup.com</p>
      </div>
    </section>
  </article>
</main>
</body>
</html>
```